Hold Steady, Marisol: Needle Of Light

I want the front cover to feature a young lady wearing an elaborate dress in the middle foreground, with a seamstress sewing away and a sewing machine nearby in the background (smaller). They are both the same girl, in her 20's with a thick braid going down 1 side of her head and elaborate beads in her hair. She is African American.
The background picture should be similar to the picture of the seamstress attached, but the girl will have a long, thick braid.

The bottom of the dress should have rows of ruffles like the black dress attached, the sleeves of the dress should be bell shaped like the brown and cream dress and the top should have slanted crystals going down the front like the red dress suit. The foreground picture should feature the girl on a runway with a few people watching.

The back cover should feature the same braid haired girl walking away in the same dress. There are multiple roses going down the dress like the colored dress in the runway picture.

In no instance should there be more than 6 people watching her walk (front nor back cover). However, a few should be standing as they watch, not sitting!

She looks confident and gorgeous. She has make-up, but not a whole lot - eyeliner with wings, long lashes, blush on cheeks and color on lips.
Please see my rough draft of the front cover image I have in mind.

BACK COVER
Back cover brief details
Author Biography
Doreen L. Whitcombe is a God-fearing Christian, who also identifies as spiritually a Hebrew. By God’s grace, she has worked as an Online/Virtual and brick-and-mortar educator in Regular Education and Special Education for 15 years.
She enjoys archery, singing, reading and writing. The mother of an adult son and mother-in-law to a precious young lady, also has two older sisters.
As an author and self-publisher of her own multi-genre titles, she has clocked almost 30 years working in this capacity. She’s blessed to do public relations and technical writing for clients and use her services as a writing consultancy for authors and people in other industries.
SUMMARY
“Hold Steady, Marisol,” is a sequel to the popular title, “Uncle Pepper’s Restless Kin.” That title featured a number of city-dwelling nieces and nephews who reluctantly visit their bossy Uncle Pepper at her countryside home for their summer vacation. This started a tradition that they began to look forward to, for Uncle Pepper was a force to be reckoned with. Marisol packed more fabric and fashion design materials in her suitcase than ready-made clothes for each visit as she was an intentional seamstress.
In this sequel, Marisol gets selected for a fashion design contest preparing an elaborate dress for an unknown female. With fewer credentials than the other contestants, she knows that God opened that door for her. The way He sustains her, time-and-time-again causes her to continue to give Him glory for all He has done.
Willing to stand without apology or hesitation for her faith and be a lifted-up standard against fashion industry norms, Marisol becomes a tour-de-force. She puts into practice something her late Uncle Pepper and parents taught her as she learns how to stand out in a good way for the right thing.

Target Market(s)

Young Adults

Industry/Entity Type

Fashion Design

Font styles to use
Decorative
Other font styles liked:
• Cambria

Requirements
Must have
• Detailed dress design. Modesty-not much skin showing.
Nice to have
• Multiple small Rosettes on the dress. Silhouette similar to the pink dress attached, but not as much of the legs showing, and not strapless.
Should not have
• A lot of people near the runway. The girl and her dress are prominent images.

```html
<!DOCTYPE html>
<html lang="en">
<head>
<meta charset="utf-8">
<title>Hold Steady, Marisol: Needle Of Light — Back Cover</title>
<link rel="stylesheet" href="https://fonts.googleapis.com/css2?family=Caladea:wght@400;700&display=swap">
<style>
  :root {
    --parchment: #d8cbb4;
    --parchment-light: #e3d8c5;
    --parchment-dark: #c9b99e;
    --ink: #2a231f;
    --royal-blue: #2f5aa8;
    --band-blue: #3560ad;
    --white: #ffffff;
    --frame-gold: #cbb98f;
  }
  * { margin: 0; padding: 0; box-sizing: border-box; }
  html, body { width: 800px; height: 1200px; overflow: hidden; }
  body { font-family: "Caladea", Cambria, serif; color: var(--ink); }

  .back-cover {
    position: relative;
    width: 800px;
    height: 1200px;
    overflow: hidden;
  }
  .cover-artwork {
    position: absolute;
    inset: 0;
    background:
      radial-gradient(ellipse 55% 70% at 65% 45%, var(--parchment-light), transparent 70%),
      linear-gradient(180deg, var(--parchment) 0%, var(--parchment-dark) 100%);
  }
  .author-portrait {
    position: absolute;
    left: 253px;
    top: 37px;
    width: 294px;
    height: 294px;
    border-radius: 50%;
    border: 2px solid var(--royal-blue);
    padding: 4px;
    background: var(--frame-gold);
  }
  .author-portrait .photo {
    width: 100%;
    height: 100%;
    border-radius: 50%;
    background: linear-gradient(160deg, #dfe2e8 0%, #b9c2d6 40%, #2c4f9e 70%, #e9e6df 100%);
  }

  .copy {
    position: absolute;
    left: 82px;
    width: 634px;
    font-size: 17px;
    line-height: 21.8px;
    text-align: justify;
    hyphens: auto;
  }
  .copy p { margin: 0; }
  .author-bio { top: 352px; }
  .author-name {
    color: var(--royal-blue);
    font-weight: 700;
    font-size: 23px;
    letter-spacing: 0.3px;
  }
  .section-divider {
    position: absolute;
    left: 229px;
    top: 605px;
    width: 350px;
    height: 2px;
    background: var(--royal-blue);
  }
  .book-summary { top: 641px; }

  .footer-band {
    position: absolute;
    left: 0;
    bottom: 0;
    width: 800px;
    height: 89px;
    background: var(--band-blue);
    z-index: 1;
  }

  .publisher {
    position: absolute;
    left: 126px;
    top: 1042px;
    display: flex;
    align-items: center;
    gap: 12px;
    z-index: 2;
  }
  .publisher-mark {
    width: 94px;
    height: 94px;
    border-radius: 50%;
    background: var(--white);
  }
  .publisher-name {
    font-family: "Caladea", Cambria, serif;
    font-size: 17px;
    color: var(--ink);
  }
</style>
</head>
<body>
  <main class="back-cover">
    <div class="cover-artwork" role="img" aria-label="Faded illustration of the seamstress at her sewing machine and the young woman with a long braid in a ruffled rose-covered gown, in soft beige tones"></div>

    <figure class="author-portrait">
      <div class="photo" role="img" aria-label="Portrait photograph of the author in a blue and gold brocade top holding a white gift box"></div>
    </figure>

    <section class="copy author-bio">
      <p><span class="author-name">Doreen L. Whitcombe</span> is a God-fearing Christian, who also identifies as spiritually a Hebrew. By God’s grace, she has worked as an Online/Virtual and brick-and-mortar educator in Regular Education and Special Education for 15 years.</p>
      <p>She enjoys archery, singing, reading and writing. The mother of an adult son and mother-in-law to a precious young lady, also has two older sisters.</p>
      <p>As an author and self-publisher of her own multi-genre titles, she has clocked almost 30 years working in this capacity. She’s blessed to do public relations and technical writing for clients and use her services as a writing consultancy for authors and people in other industries.</p>
    </section>

    <div class="section-divider"></div>

    <section class="copy book-summary">
      <p>“Hold Steady, Marisol,” is a sequel to the popular title, “Uncle Pepper’s Rest&shy;less Kin.” That title featured a number of city-dwelling nieces and nephews who reluctantly visit their bossy Uncle Pepper at her countryside home for their summer vacation. This started a tradition that they began to look forward to, for Uncle Pepper was a force to be reckoned with. Marisol packed more fabric and fashion design materials in her suitcase than ready-made clothes for each visit as she was an intentional seamstress.</p>
      <p>In this sequel, Marisol gets selected for a fashion design contest preparing an elaborate dress for an unknown female. With fewer credentials than the other contestants, she knows that God opened that door for her. The way He sustains her, “time-and-time-again” causes her to continue to give Him glory for all He has done.</p>
      <p>Willing to stand without apology or hesitation for her faith and be a lifted-up standard against fashion industry norms, Marisol becomes a tour-de-force. She puts into practice something her late Uncle Pepper and parents taught her as she learns how to stand out in a good way for the right thing.</p>
    </section>

    <div class="footer-band"></div>

    <div class="publisher">
      <span class="publisher-mark"></span>
      <span class="publisher-name">Quillmark Press</span>
    </div>
  </main>
</body>
</html>
```